Heating and Cooling Company mobile website

We need a website specifically designed for a viewing on a mobile device.

We serve the northern New Jersey heating, cooling and electrical residential market.

The goal is the drive traffic to the site by using Brintel Pay Per click. People will be searching for an HVAC contractor, and they land on our page. They need to get key info quickly without all the clutter of a desktop type of site.

Target Market(s)

Homeowners

Industry/Entity Type

Hvac

Coding

Coded - Design and coding required

Number of Pages Required

5+ page

Font styles to use
Serif

Requirements
Must have
• View attachments to see samples of the desktop version. It must have a similar color scheme
• The copy of the website is also attached
Nice to have
• Would like it to have a sort of Vardok feel to it. Make it seem like its an app that people are using and that its exciting to be on the website. It would be nice to have a page where customers can book appointments

```html
<!DOCTYPE html>
<html lang="en">
<head>
<meta charset="utf-8">
<title>Hearthline Climate — Mobile</title>
<link href="https://fonts.googleapis.com/css2?family=Figtree:wght@400;600;700&display=swap" rel="stylesheet">
<style>
  :root {
    --cream: #ebe3cf;
    --navy: #2a2f4a;
    --maroon-deep: #5e101c;
    --maroon: #790020;
    --orange: #f0822a;
    --orange-edge: #f6c88f;
    --text-light: #f3ece4;
    --white: #ffffff;
  }
  * { box-sizing: border-box; margin: 0; padding: 0; }
  html, body {
    width: 752px;
    height: 1200px;
    overflow: hidden;
  }
  body {
    font-family: "Figtree", "Helvetica Neue", Arial, sans-serif;
    background: var(--maroon);
    color: var(--text-light);
  }
  .site { width: 752px; height: 1200px; display: flex; flex-direction: column; }

  .top-band { height: 108px; background: var(--cream); }
  .stripe {
    height: 23px;
    background: var(--navy);
    border-bottom: 4px solid var(--cream);
  }

  .contact-panel {
    height: 761px;
    background: var(--maroon-deep);
    text-align: center;
    padding-top: 24px;
  }
  .brand {
    display: inline-flex;
    align-items: center;
    gap: 16px;
    height: 56px;
    font-size: 44px;
    font-weight: 700;
    color: var(--orange-edge);
    letter-spacing: 0.5px;
  }
  .brand-mark {
    width: 22px;
    height: 22px;
    border-radius: 50%;
    background: var(--orange);
  }
  .address {
    font-style: normal;
    margin-top: 119px;
    font-size: 28px;
    line-height: 47px;
  }
  .stay-title {
    margin-top: 87px;
    font-size: 30px;
    line-height: 38px;
    font-weight: 600;
    letter-spacing: 0.5px;
    color: var(--white);
  }
  .social-links {
    display: flex;
    justify-content: center;
    align-items: center;
    gap: 22px;
    list-style: none;
    margin: 57px auto 0;
    width: 346px;
    height: 90px;
    background: var(--orange);
    border-radius: 6px;
    font-size: 21px;
    font-weight: 600;
    color: var(--white);
  }

  .footer-nav {
    flex: 1;
    background: var(--maroon);
    display: flex;
    padding: 59px 0 0 63px;
  }
  .nav-col { list-style: none; font-size: 28px; line-height: 47px; }
  .nav-col.main { width: 344px; }
  .nav-col .heading { font-weight: 700; color: var(--white); }
</style>
</head>
<body>
<div class="site">
  <header>
    <div class="top-band"></div>
    <div class="stripe"></div>
  </header>

  <section class="contact-panel">
    <div class="brand"><span class="brand-mark"></span>Hearthline Climate</div>
    <address class="address">
      24 Alder Court<br>
      Brookfield, NJ 07015<br>
      555.014.2280<br>
      hello@hearthlineclimate.com
    </address>
    <h2 class="stay-title">STAY CONNECTED</h2>
    <ul class="social-links" role="img" aria-label="Orange ribbon banner holding the social media links">
      <li>Friendfold</li>
      <li>Chirply</li>
      <li>Circlo</li>
    </ul>
  </section>

  <nav class="footer-nav">
    <ul class="nav-col main">
      <li>Home</li>
      <li>About</li>
      <li>Services</li>
      <li>Testimonials</li>
      <li>Blog</li>
      <li>Contact</li>
    </ul>
    <ul class="nav-col services">
      <li class="heading">Heating</li>
      <li>New installation</li>
      <li>Repair &amp; Service</li>
      <li>Heat Pumps</li>
      <li>Boilers</li>
      <li>Radiant Heat Systems</li>
    </ul>
  </nav>
</div>
</body>
</html>
```